Business Card Design for Retail Product Line

We need a two-sided, full-color business card for a new oral care product line. The feel of the card should invoke emotions of happiness and health. It should be bright, cheerful and modern in appearance. The card should be mostly matte finish, but with elements of spot-gloss and/or raised/embossed features (print, logo, tag lines, etc.).

Target Market(s)

People who are into whole-body health, eat well and understand the importance of nutrition.

Industry/Entity Type

Health And Wellness

Contact Information for Business Card

The logo, color scheme and tag-lines have all been developed and artwork is attached. Card is to be standard-sized and should use a mix of clean, sans-serif fonts; the main font (DIN) is attached as well. The card will be used for 3 individuals and should include placeholders for:
1. Name
2. Title (for example, "CEO")
3. Business address
4. Phone number
5. Website
6. Email address

Font styles to use
Sans Serif
Other font styles liked:
• DIN font

Colors
faa54b
000000
5c5c5c
a2ce44

Requirements
Must have
• 2 sides
• Full color orange on one side
• Image of DNA leaves
• Tag line "Smile from the Inside Out", on single side with orange background
• Company Logo (Plure) on same side as text (name, phone, address, etc.)
• Name, Title, Business Address, Phone Number, Website, Email address
• UPDATE: "Brisk Meadow", not "Brisk M Eadow"
Should not have
• Calligraphy
• Dark colors
• UPDATE!! Do not include "Turmeric infused toothpaste" on the business card
• UPDATE #2!! Do not include "Brisk Meadow" on the business card

```html
<!DOCTYPE html>
<html lang="en">
<head>
<meta charset="utf-8">
<title>Plure Business Card</title>
<link href="https://fonts.googleapis.com/css2?family=Open+Sans:wght@400;600;700;800&display=swap" rel="stylesheet">
<style>
  :root {
    --page-bg: #e9e9e9;
    --card-white: #fbfbfb;
    --brand-orange: #faa54b;
    --orange-deep: #e9a83a;
    --orange-glow: #f6dc3e;
    --text-dark: #3a3a3a;
    --text-grey: #5c5c5c;
    --white: #ffffff;
  }
  * { margin: 0; padding: 0; box-sizing: border-box; }
  html, body {
    width: 1200px;
    height: 900px;
    overflow: hidden;
    background: var(--page-bg);
    font-family: "Open Sans", Arial, sans-serif;
  }
  .canvas {
    position: relative;
    width: 1200px;
    height: 900px;
  }
  .card {
    position: absolute;
    top: 300px;
    width: 525px;
    height: 300px;
    border-radius: 3px;
    box-shadow: 0 10px 28px rgba(0,0,0,0.12), 0 2px 6px rgba(0,0,0,0.08);
    overflow: hidden;
  }
  /* Front side */
  .card-front {
    left: 50px;
    background: var(--card-white);
  }
  .brand-name {
    position: absolute;
    left: 48px;
    top: 108px;
    font-weight: 700;
    font-size: 60px;
    line-height: 1;
    color: var(--brand-orange);
    letter-spacing: -0.5px;
  }
  .contact {
    position: absolute;
    left: 290px;
    top: 92px;
    color: var(--text-dark);
    font-size: 12.5px;
    line-height: 1.35;
  }
  .contact-name {
    color: var(--brand-orange);
    font-weight: 700;
    font-size: 15px;
  }
  .contact-title { margin-bottom: 10px; }
  .contact-address { margin-bottom: 10px; }
  .contact-line {
    display: flex;
    align-items: center;
    gap: 8px;
  }
  .contact-line svg { flex: none; }
  /* Back side */
  .card-back {
    left: 625px;
    background: radial-gradient(ellipse 55% 60% at 50% 50%, var(--orange-glow) 0%, #f2c73c 45%, var(--orange-deep) 100%);
    display: flex;
    align-items: center;
    justify-content: center;
  }
  .tagline {
    color: var(--white);
    font-weight: 800;
    line-height: 0.92;
    text-transform: uppercase;
    text-align: left;
  }
  .tagline-main {
    font-size: 78px;
    text-transform: lowercase;
    letter-spacing: -1px;
  }
  .tagline-sub {
    font-size: 33px;
    font-weight: 700;
    letter-spacing: 0.5px;
  }
</style>
</head>
<body>
<main class="canvas">
  <section class="card card-front" aria-label="Business card front">
    <div class="brand-name">Plure</div>
    <div class="contact">
      <div class="contact-name">Daniel Harper</div>
      <div class="contact-title">Managing Director</div>
      <div class="contact-address">1234, Address GoesHere,<br>Country, 12345</div>
      <div class="contact-line">
        <svg width="9" height="9" viewBox="0 0 10 10" aria-hidden="true"><path d="M2 1h2l1 2.5-1.3.8a6 6 0 0 0 2 2l.8-1.3L9 6v2a1 1 0 0 1-1 1A7 7 0 0 1 1 2a1 1 0 0 1 1-1z" fill="var(--brand-orange)"/></svg>
        <span>(044) 123 456 789</span>
      </div>
      <div class="contact-line">
        <svg width="9" height="9" viewBox="0 0 10 10" aria-hidden="true"><rect x="0.5" y="2" width="9" height="6.5" rx="1" fill="var(--brand-orange)"/><path d="M1 2.5l4 3 4-3" stroke="#fff" stroke-width="0.9" fill="none"/></svg>
        <span>info@youremail.com</span>
      </div>
      <div class="contact-line">
        <svg width="9" height="9" viewBox="0 0 10 10" aria-hidden="true"><circle cx="5" cy="5" r="4.5" fill="var(--brand-orange)"/><path d="M0.5 5h9M5 0.5c-2 2.5-2 6.5 0 9M5 0.5c2 2.5 2 6.5 0 9" stroke="#fff" stroke-width="0.7" fill="none"/></svg>
        <span>www.webname.com</span>
      </div>
    </div>
  </section>

  <section class="card card-back" aria-label="Business card back">
    <div class="tagline">
      <div class="tagline-main">beam</div>
      <div class="tagline-sub">Bright and</div>
      <div class="tagline-sub">Well within</div>
    </div>
  </section>
</main>
</body>
</html>
```